Calvanto Group Real Estate Company business cards

New business card design, we are generally happy with the basic layout of the existing front of business card, (feel free to change) but require a head shot photo on the back side.

http://www.calvanto.com.au/

Attached logos, and existing business card

------------------------------

Target Market(s)

Real estate

Industry/Entity Type

Real Estate

Contact Information for Business Card

Standard size double sided

Font styles to use
Other font styles liked:
• Futura

Requirements
Must have
• Photo head shot on the back side
Nice to have
• yes
Should not have
• No

```html
<!DOCTYPE html>
<html lang="en">
<head>
<meta charset="utf-8">
<title>Calvanto Group – Business Cards</title>
<link rel="stylesheet" href="https://fonts.googleapis.com/css2?family=Open+Sans:wght@400;600;700&display=swap">
<style>
  :root {
    --purple: #2e2260;
    --purple-deep: #251a52;
    --orange: #f0901e;
    --white: #ffffff;
    --grey-bg: #3a3b40;
    --photo-light: #e6e8ea;
    --photo-mid: #c9ccd2;
  }
  * { box-sizing: border-box; margin: 0; padding: 0; }
  html, body {
    width: 1200px; height: 864px; overflow: hidden;
    background: var(--grey-bg);
    font-family: "Open Sans", Arial, sans-serif;
  }
  .stage { position: relative; width: 1200px; height: 864px; }
  .card {
    position: absolute; left: 320px; width: 560px; height: 342px;
    overflow: hidden; border-radius: 3px;
    box-shadow: 0 8px 24px rgba(0,0,0,.35);
  }
  /* Front */
  .card--front { top: 60px; background: var(--white); }
  .brand {
    position: absolute; top: 92px; left: 0; width: 100%;
    text-align: center; color: var(--purple);
    font-size: 52px; font-weight: 600; letter-spacing: -0.5px; line-height: 1;
  }
  .tagline {
    position: absolute; top: 178px; left: 0; width: 100%;
    text-align: center; color: var(--purple);
    font-size: 16px; font-weight: 700; letter-spacing: .3px;
  }
  .services-band {
    position: absolute; top: 212px; left: 0; width: 100%; height: 66px;
    background: var(--purple); border-bottom: 4px solid var(--orange);
    display: flex; align-items: center; justify-content: center;
    color: var(--white); font-size: 17px; font-weight: 700; letter-spacing: .5px;
  }
  /* Back */
  .card--back { top: 442px; background: var(--purple); }
  .headshot {
    position: absolute; left: 36px; top: 56px; width: 230px; height: 230px;
    border-radius: 50%;
    background: radial-gradient(circle at 50% 45%, var(--photo-light) 0%, var(--photo-mid) 70%, var(--purple) 100%);
  }
  .details { position: absolute; left: 300px; top: 82px; color: var(--white); }
  .details__name { color: var(--orange); font-size: 21px; font-weight: 700; }
  .details__role { font-size: 14px; margin-top: 2px; }
  .details__company { color: var(--orange); font-size: 17px; font-weight: 700; margin-top: 16px; }
  .details__abn { font-size: 14px; margin-top: 2px; }
  .details__abn b { font-weight: 700; }
  .contacts { list-style: none; margin-top: 18px; }
  .contacts li { display: flex; align-items: center; gap: 12px; font-size: 14.5px; line-height: 25px; }
  .contacts svg { width: 13px; height: 13px; fill: var(--orange); flex: none; }
</style>
</head>
<body>
<main class="stage">
  <section class="card card--front" aria-label="Business card front">
    <div class="brand">Calvanto Group</div>
    <div class="tagline">LET US SHOW YOU PROPERTY</div>
    <div class="services-band">Buy&nbsp; | &nbsp;Sell&nbsp; | &nbsp;Rent</div>
  </section>

  <section class="card card--back" aria-label="Business card back">
    <div class="headshot" role="img" aria-label="Head shot photo of the director"></div>
    <div class="details">
      <div class="details__name">Daniel Tran</div>
      <div class="details__role">Director</div>
      <div class="details__company">Calvanto Group</div>
      <div class="details__abn"><b>ABN:</b> 12 345 678 901</div>
      <ul class="contacts">
        <li>
          <svg viewBox="0 0 24 24" aria-hidden="true"><path d="M6.6 10.8a15.1 15.1 0 0 0 6.6 6.6l2.2-2.2c.3-.3.7-.4 1-.2 1.1.4 2.3.6 3.6.6.6 0 1 .4 1 1V20c0 .6-.4 1-1 1C10.6 21 3 13.4 3 4c0-.6.4-1 1-1h3.5c.6 0 1 .4 1 1 0 1.3.2 2.5.6 3.6.1.3 0 .7-.2 1z"/></svg>
          0400 555 218
        </li>
        <li>
          <svg viewBox="0 0 24 24" aria-hidden="true"><path d="M2 5h20v14H2z M3 6l9 7 9-7" /></svg>
          daniel.tran@calvanto.com.au
        </li>
        <li>
          <svg viewBox="0 0 24 24" aria-hidden="true"><circle cx="12" cy="12" r="10"/></svg>
          www.calvanto.com.au
        </li>
      </ul>
    </div>
  </section>
</main>
</body>
</html>
```